Home Page and One Inside Page Needed for Engine Modify Site

Website that sells kits to modify and enhance your car engine performance. I don't like direction / design of current site at http://www.vaxorspeedlab.com.php53-17.ord1-1.draftpreviewbox.com/

I want something modern. Something that shows power and performance.

I need home page and one inside page.

Keep blues and blacks and unfortunately that is their logo we have to work with. But this site needs WOW factor.

YOU DO NOT HAVE PERMISSION TO WORK OR SPEAK TO CLIENT DIRECTLY AND MUST WORK THROUGH ME.

```html
<!DOCTYPE html>
<html lang="en">
<head>
<meta charset="utf-8">
<title>vaxorspeedlab – precision exhaust header modeling system</title>
<link href="https://fonts.googleapis.com/css2?family=PT+Sans:wght@400;700&display=swap" rel="stylesheet">
<style>
:root{
  --blue:#2f2cf6;
  --blue-deep:#1410c4;
  --blue-btn:#1f1ff0;
  --ink:#1b1b1b;
  --white:#ffffff;
  --grey-bg:#efefef;
  --grey-text:#6a6a6a;
  --footer:#1f222a;
  --footer-text:#8b8f98;
  --hero-dark:#07081a;
}
*{margin:0;padding:0;box-sizing:border-box}
html,body{width:1006px;height:1200px;overflow:hidden;background:var(--white)}
body{position:relative;font-family:"PT Sans",Arial,sans-serif;color:var(--ink)}
.abs{position:absolute}
ul{list-style:none}

/* header */
.topbar{left:158px;top:0;width:181px;height:4px;background:var(--ink)}
.brand{left:157px;top:22px;font-size:27px;font-weight:700;color:var(--blue-btn);letter-spacing:-.3px;line-height:32px}
.tagline{left:157px;top:53px;font-size:9px;color:var(--ink);letter-spacing:.2px}
.nav{left:424px;top:31px;display:flex;align-items:center;height:22px;font-size:11px}
.nav a{color:var(--ink);text-decoration:none;padding:0 11px;border-left:1px solid #c9c9c9;line-height:12px}
.nav a.active{background:var(--blue-btn);color:var(--white);border:0;border-radius:2px;line-height:22px;padding:0 9px;margin-right:1px}
.nav a.active + a{border-left:0}

/* hero */
.hero{left:0;top:84px;width:1006px;height:337px;background:radial-gradient(ellipse 420px 260px at 330px 170px,#1b2bd8 0%,#0d1270 45%,var(--hero-dark) 85%)}
.hero-media{left:156px;top:104px;width:396px;height:292px;border-radius:40px;background:radial-gradient(ellipse at 50% 50%,#c9622a 0%,#9a9ca8 40%,#3a3f60 80%,transparent 100%)}
.hero-copy{left:610px;top:216px;width:250px;font-size:10.5px;line-height:13px;color:var(--white);font-weight:700}
.btn-more{left:610px;top:290px;width:65px;height:23px;background:var(--blue-btn);color:var(--white);font-size:11px;font-weight:700;display:flex;align-items:center;justify-content:center;border-radius:1px}
.hero-arrow{top:206px}

/* blue band */
.band{left:0;top:421px;width:1006px;height:329px;background:var(--blue)}
.band-title{font-size:13px;font-weight:700;color:var(--white);text-transform:uppercase;letter-spacing:-.2px}
.pager{display:flex;gap:3px}
.pager span{width:12px;height:12px;background:#1a1a3a;display:flex;align-items:center;justify-content:center}
.panel{background:var(--blue-deep)}
.who-panel{left:158px;top:463px;width:434px;height:133px}
.who-media{left:173px;top:480px;width:185px;height:102px;background:linear-gradient(135deg,#e8e8ee 0%,#8d8f9e 40%,#262833 75%,#111 100%)}
.who-copy{left:369px;top:484px;width:215px;font-size:10px;line-height:13px;color:var(--white)}
.gallery-item{top:630px;height:86px}
.divider{left:614px;top:436px;width:1px;height:276px;background:rgba(0,0,40,.35)}
.cats{left:631px;top:470px;font-size:10px;color:var(--white)}
.cats li{height:17.3px;display:flex;align-items:center;gap:8px}
.mechanic{left:736px;top:432px;width:88px;height:162px;border-radius:44px 44px 8px 8px;background:linear-gradient(180deg,#3a4460 0%,#1f2740 70%,#b52233 100%)}
.news-panel{left:632px;top:630px;width:215px;height:86px;padding:11px 10px;font-size:10px;line-height:13px;color:var(--white)}
.news-panel b{font-weight:700}

/* features */
.features{left:0;top:750px;width:1006px;height:221px;background:var(--grey-bg)}
.feature{top:782px;width:216px;text-align:center}
.feature-media{width:216px;height:92px}
.feature-title{margin-top:15px;font-size:10.5px;color:var(--blue-btn);text-transform:uppercase;display:flex;justify-content:center;align-items:center;gap:6px}
.feature-copy{margin-top:13px;font-size:10px;line-height:13px;color:var(--grey-text)}

/* footer */
.footer{left:0;top:971px;width:1006px;height:181px;background:var(--footer)}
.foot-title{top:1000px;font-size:12.5px;color:var(--white)}
.foot-nav{left:157px;top:1021px;font-size:10px;color:var(--footer-text)}
.foot-nav li{height:18px;display:flex;align-items:center;gap:6px}
.social{left:322px;top:1025px;font-size:10px;color:var(--footer-text)}
.social li{height:31px;display:flex;align-items:center;gap:12px}
.social i{width:15px;height:15px;background:#d8d8d8;border-radius:2px;display:block}
.contact{left:476px;top:1023px;font-size:10px;line-height:14.4px;color:#6e727b}
.email-field{left:663px;top:1024px;width:184px;height:22px;border:1px solid #4a4d55;background:#15171d;font-size:9px;color:#5c6069;padding-left:7px;display:flex;align-items:center}
.btn-sub{left:663px;top:1054px;width:55px;height:20px;background:var(--white);color:var(--ink);font-size:10px;display:flex;align-items:center;justify-content:center;border-radius:2px}
.copyright{left:159px;top:1159px;font-size:10px;color:#555}
</style>
</head>
<body>

<header>
  <div class="abs topbar"></div>
  <div class="abs brand">vaxorspeedlab</div>
  <div class="abs tagline">precision exhaust header modeling system</div>
  <nav class="abs nav">
    <a class="active">HOME</a><a>ABOUT US</a><a>PRODUCT</a><a>RESOURCES</a><a>HOW IT WORKS</a><a>CONTACT US</a>
  </nav>
</header>

<section>
  <div class="abs hero"></div>
  <div class="abs hero-media" role="img" aria-label="Chrome and orange V8 engine with exhaust headers"></div>
  <svg class="abs hero-arrow" style="left:76px" width="42" height="96" viewBox="0 0 42 96"><polyline points="41,1 1,48 41,95" fill="none" stroke="#8a8fb0" stroke-width="1.5"/></svg>
  <svg class="abs hero-arrow" style="left:883px" width="42" height="96" viewBox="0 0 42 96"><polyline points="1,1 41,48 1,95" fill="none" stroke="#8a8fb0" stroke-width="1.5"/></svg>
  <p class="abs hero-copy">Lorem Ipsum is simply dummy text of the printing and typesetting industry. Lorem Ipsum has been the industry's standard dummy text ever since the 1500s, when an unknown printer took a galley of type and survived not only five centuries,</p>
  <div class="abs btn-more">MORE</div>
</section>

<section>
  <div class="abs band"></div>

  <h2 class="abs band-title" style="left:158px;top:438px">Who is using it?</h2>
  <div class="abs pager" style="left:565px;top:441px"><span><svg width="7" height="6"><path d="M6 3H1M3 1L1 3L3 5" stroke="#fff" fill="none"/></svg></span><span><svg width="7" height="6"><path d="M1 3H6M4 1L6 3L4 5" stroke="#fff" fill="none"/></svg></span></div>
  <div class="abs panel who-panel"></div>
  <div class="abs who-media" role="img" aria-label="Polished exhaust headers under a white sports car"></div>
  <p class="abs who-copy">Lorem Ipsum is :<br>when an unknown printer took a galley of type and scrambled it to make a type specimen book. It has survived not only five centuries, but also the leap into electronic typesetting, remaining essentially unchanged. It was popularised in the 1960s with the release of Letraset sheets containing</p>

  <h2 class="abs band-title" style="left:157px;top:610px">Our Gallery</h2>
  <div class="abs pager" style="left:565px;top:612px"><span><svg width="7" height="6"><path d="M6 3H1M3 1L1 3L3 5" stroke="#fff" fill="none"/></svg></span><span><svg width="7" height="6"><path d="M1 3H6M4 1L6 3L4 5" stroke="#fff" fill="none"/></svg></span></div>
  <div class="abs gallery-item" style="left:158px;width:139px;background:linear-gradient(135deg,#e5e7ec,#2c4a6a 55%,#101418)" role="img" aria-label="Blue engine bay"></div>
  <div class="abs gallery-item" style="left:306px;width:139px;background:linear-gradient(160deg,#d6d8dc,#6b6e74 50%,#1a1b1e)" role="img" aria-label="Engine manifold close-up"></div>
  <div class="abs gallery-item" style="left:452px;width:140px;background:linear-gradient(120deg,#2a2620,#9a8a70 50%,#151515)" role="img" aria-label="Hand working on an engine"></div>

  <div class="abs divider"></div>

  <h2 class="abs band-title" style="left:631px;top:438px">Our Categories</h2>
  <ul class="abs cats">
    <li><svg width="10" height="6"><path d="M0 3H9M6 0.5L9 3L6 5.5" stroke="#fff" fill="none"/></svg>1625 Series</li>
    <li><svg width="10" height="6"><path d="M0 3H9M6 0.5L9 3L6 5.5" stroke="#fff" fill="none"/></svg>1750 Series</li>
    <li><svg width="10" height="6"><path d="M0 3H9M6 0.5L9 3L6 5.5" stroke="#fff" fill="none"/></svg>2000 Series</li>
    <li><svg width="10" height="6"><path d="M0 3H9M6 0.5L9 3L6 5.5" stroke="#fff" fill="none"/></svg>FAbrication tools</li>
    <li><svg width="10" height="6"><path d="M0 3H9M6 0.5L9 3L6 5.5" stroke="#fff" fill="none"/></svg>Home</li>
    <li><svg width="10" height="6"><path d="M0 3H9M6 0.5L9 3L6 5.5" stroke="#fff" fill="none"/></svg>pre-bent tubing</li>
    <li><svg width="10" height="6"><path d="M0 3H9M6 0.5L9 3L6 5.5" stroke="#fff" fill="none"/></svg>Uncategorized</li>
  </ul>
  <div class="abs mechanic" role="img" aria-label="Mechanic in overalls holding a wrench and a red toolbox"></div>

  <h2 class="abs band-title" style="left:631px;top:610px">Latest News</h2>
  <div class="abs pager" style="left:820px;top:612px"><span><svg width="7" height="6"><path d="M6 3H1M3 1L1 3L3 5" stroke="#fff" fill="none"/></svg></span><span><svg width="7" height="6"><path d="M1 3H6M4 1L6 3L4 5" stroke="#fff" fill="none"/></svg></span></div>
  <div class="abs panel news-panel"><b>17-7-2013 :</b> Lorem Ipsum is simply dummy text of the printing and typesetting industry. Lorem Ipsum has been type and survived not only five centuries,</div>
</section>

<section>
  <div class="abs features"></div>
  <article class="abs feature" style="left:158px">
    <div class="feature-media" style="background:linear-gradient(135deg,#2b3a5a,#8a6a5a 45%,#b3242a 75%,#3a2a20)" role="img" aria-label="Technician working on an engine"></div>
    <h3 class="feature-title">System Features <svg width="6" height="10"><path d="M1 1L5 5L1 9" stroke="#1f1ff0" fill="none" stroke-width="1.3"/></svg></h3>
    <p class="feature-copy">Lorem Ipsum is simply dummy text of the printing and typesetting industry. Lorem Ipsum has been type and survived not only five centuries,</p>
  </article>
  <article class="abs feature" style="left:395px">
    <div class="feature-media" style="background:linear-gradient(135deg,#3a2414,#c89a6a 45%,#6a4426 75%,#1a0e08)" role="img" aria-label="Bronze-toned engine pipes"></div>
    <h3 class="feature-title">How It Works <svg width="6" height="10"><path d="M1 1L5 5L1 9" stroke="#1f1ff0" fill="none" stroke-width="1.3"/></svg></h3>
    <p class="feature-copy">Lorem Ipsum is simply dummy text of the printing and typesetting industry. Lorem Ipsum has been type and survived not only five centuries,</p>
  </article>
  <article class="abs feature" style="left:632px">
    <div class="feature-media" style="background:linear-gradient(135deg,#1a1a1e,#d0d2d8 45%,#4a4c58 70%,#101012)" role="img" aria-label="Chrome motorcycle exhaust"></div>
    <h3 class="feature-title">Our Gallery <svg width="6" height="10"><path d="M1 1L5 5L1 9" stroke="#1f1ff0" fill="none" stroke-width="1.3"/></svg></h3>
    <p class="feature-copy">Lorem Ipsum is simply dummy text of the printing and typesetting industry. Lorem Ipsum has been type and survived not only five centuries,</p>
  </article>
</section>

<footer>
  <div class="abs footer"></div>
  <h4 class="abs foot-title" style="left:157px">Navigation</h4>
  <ul class="abs foot-nav">
    <li><svg width="8" height="6"><path d="M0 3H7M5 1L7 3L5 5" stroke="#fff" fill="none"/></svg>Home</li>
    <li><svg width="8" height="6"><path d="M0 3H7M5 1L7 3L5 5" stroke="#8b8f98" fill="none"/></svg>About Us</li>
    <li><svg width="8" height="6"><path d="M0 3H7M5 1L7 3L5 5" stroke="#8b8f98" fill="none"/></svg>Product</li>
    <li><svg width="8" height="6"><path d="M0 3H7M5 1L7 3L5 5" stroke="#8b8f98" fill="none"/></svg>Resources</li>
    <li><svg width="8" height="6"><path d="M0 3H7M5 1L7 3L5 5" stroke="#8b8f98" fill="none"/></svg>How It Works</li>
    <li><svg width="8" height="6"><path d="M0 3H7M5 1L7 3L5 5" stroke="#8b8f98" fill="none"/></svg>Contact Us</li>
  </ul>

  <h4 class="abs foot-title" style="left:313px">Connect with Us</h4>
  <ul class="abs social">
    <li><i></i>Friendwall</li>
    <li><i></i>Chirpline</li>
    <li><i></i>ViewCast</li>
  </ul>

  <h4 class="abs foot-title" style="left:474px">Contact Address</h4>
  <address class="abs contact" style="font-style:normal">48 Corliss Lane Harmon,<br>TX 70412<br>Phone: (555) 014 2270<br>Fax: (555) 014 2291<br>M-F 9-6<br>Email: info@vaxorspeedlab.com</address>

  <h4 class="abs foot-title" style="left:663px">Subscribe for News Letter</h4>
  <div class="abs email-field">Your &nbsp;E-mail ID</div>
  <div class="abs btn-sub">Subscribe</div>

  <p class="abs copyright">2013 © Allright Reserved by vaxorspeedlab</p>
</footer>

</body>
</html>
```